Business card for Internet Marketing Consultant

Simple - need a nice business card design using the logo elements and colors. Keywords: Progressive, professional, stylish, minimalist. Please use the nb as part of the design.

Info for card:

Brendan Okafor
Internet Marketing Strategist
Phone: (520) 555-0148
Email: brendan@northbeamgrowth.com
Address: 2193 W. Larkmoor Ave., Ste. 118
Tucson, Arizona 85710

Website: www.northbeamgrowth.com

Industry/Entity Type

Business

Font styles to use
Sans Serif

```html
<!DOCTYPE html>
<html lang="en">
<head>
<meta charset="utf-8">
<title>Northbeam Growth – Business Card</title>
<link rel="stylesheet" href="https://fonts.googleapis.com/css2?family=Source+Sans+3:wght@400;600;700&display=swap">
<style>
  :root {
    --backdrop: #2e241f;
    --card-white: #ffffff;
    --brand-blue: #2f6bb8;
    --brand-green: #6abf74;
    --brand-green-deep: #58a963;
    --ink: #3d3d3d;
    --label: #ffffff;
  }
  * { margin: 0; padding: 0; box-sizing: border-box; }
  html, body {
    width: 1200px; height: 782px; overflow: hidden;
    background: var(--backdrop);
    font-family: "Source Sans 3", sans-serif;
  }
  .canvas { position: relative; width: 1200px; height: 782px; }
  .card {
    position: absolute; width: 464px; height: 266px; overflow: hidden;
    box-shadow: 0 4px 10px rgba(0,0,0,.35);
  }
  .card--front { left: 364px; top: 80px; background: var(--card-white); }
  .card--back-green { left: 110px; top: 396px; background: var(--brand-green); }
  .card--back-white { left: 630px; top: 394px; background: var(--card-white); }

  .name-tab {
    position: absolute; left: 0; top: 29px; width: 239px; height: 43px;
    background: var(--brand-blue); border-radius: 0 12px 12px 0;
    padding: 4px 0 0 29px; color: #fff;
  }
  .name-tab__name { font-size: 18px; font-weight: 700; line-height: 20px; }
  .name-tab__title { font-size: 11px; line-height: 14px; }

  .wordmark {
    position: absolute; display: flex; align-items: center; gap: 8px;
  }
  .wordmark__dot { width: 30px; height: 30px; border-radius: 50%; background: var(--brand-green); }
  .wordmark__name { font-size: 30px; font-weight: 600; color: var(--brand-blue); letter-spacing: -.3px; }
  .card--front .wordmark { left: 29px; top: 108px; }
  .card--back-white .wordmark { left: 0; right: 0; top: 112px; justify-content: center; }

  .contact { position: absolute; left: 29px; top: 204px; font-size: 11px; color: var(--ink); }
  .contact__row { display: flex; align-items: center; gap: 6px; height: 16px; }
  .contact__row svg { width: 10px; height: 10px; fill: var(--brand-blue); }
  .divider { position: absolute; left: 256px; top: 222px; width: 1.5px; height: 25px; background: var(--brand-green); }
  .address { position: absolute; left: 282px; top: 220px; font-size: 11px; line-height: 16px; color: var(--ink); }

  .back-url {
    position: absolute; left: 43px; top: 40px; color: #fff;
    font-size: 12px; font-weight: 600; letter-spacing: 2px;
  }
  .back-circle {
    position: absolute; left: 10px; top: 120px; width: 200px; height: 200px;
    border-radius: 50%; background: var(--brand-green-deep);
  }
  .option-label { position: absolute; color: var(--label); font-size: 34px; font-weight: 400; }
  .option-label--one { left: 112px; top: 680px; }
  .option-label--two { left: 632px; top: 690px; }
</style>
</head>
<body>
<main class="canvas">
  <section class="card card--front">
    <div class="name-tab">
      <div class="name-tab__name">Brendan Okafor</div>
      <div class="name-tab__title">Internet Marketing Strategist</div>
    </div>
    <div class="wordmark">
      <span class="wordmark__dot"></span>
      <span class="wordmark__name">northbeamgrowth</span>
    </div>
    <div class="contact">
      <div class="contact__row">
        <svg viewBox="0 0 10 10"><path d="M2 0.5 L4 2.5 L3 3.8 Q4 6 6.2 7 L7.5 6 L9.5 8 L8 9.6 Q3.5 9 0.5 2 Z"/></svg>
        <span>(520) 555-0148</span>
      </div>
      <div class="contact__row">
        <svg viewBox="0 0 10 10"><path d="M0.5 2 H9.5 V8.5 H0.5 Z M1 2.5 L5 5.5 L9 2.5" stroke="#fff" stroke-width=".8"/></svg>
        <span>brendan@northbeamgrowth.com</span>
      </div>
      <div class="contact__row">
        <svg viewBox="0 0 10 10"><circle cx="5" cy="5" r="4.5"/><path d="M0.5 5 H9.5 M5 0.5 V9.5 M5 0.5 Q2 5 5 9.5 Q8 5 5 0.5" stroke="#fff" stroke-width=".7" fill="none"/></svg>
        <span>www.northbeamgrowth.com</span>
      </div>
    </div>
    <div class="divider"></div>
    <div class="address">2193 W. Larkmoor Ave., Ste.<br>118, Tucson, Arizona 85710</div>
  </section>

  <section class="card card--back-green">
    <div class="back-circle"></div>
    <div class="back-url">www.northbeamgrowth.com</div>
  </section>

  <section class="card card--back-white">
    <div class="wordmark">
      <span class="wordmark__dot"></span>
      <span class="wordmark__name">northbeamgrowth</span>
    </div>
  </section>

  <p class="option-label option-label--one">Back option 1</p>
  <p class="option-label option-label--two">Back option 2</p>
</main>
</body>
</html>
```